Pyschiatry Experts need Marketing Campaign

Ad(s) developed for print advertising sharing our purpose and services, highlighting our medical care providers. Must be welcoming and inviting while displaying a high level of professionalism expected from a physician's office.

Target Market(s)

Local community

Industry/Entity Type

Psychiatry (Healthcare)

Requirements
Must have
• Staff pictures, 'Medication Management Experts', 'Prompt Appointments', 'ADD/ADHD, Bipolar Disorder, Depression, Anxiety, Schizophrenia, Grief Reaction and others' 'Virtual and In-Person Visits'
Nice to have
• Address: 412 E Marlowe Coeur d'Alene Phone (208)555-7193 website: BrightLoftCare.com Hours: Mon - Thur 7am - 6pm

```html
<!DOCTYPE html>
<html lang="en">
<head>
<meta charset="utf-8">
<title>Bright Loft Care – Mental Health Evaluations</title>
<link rel="stylesheet" href="https://fonts.googleapis.com/css2?family=Montserrat:wght@600;700;800&family=Poppins:wght@400;500;600;700&display=swap">
<style>
  :root {
    --teal: #0f9482;
    --lime: #8fd14f;
    --forest: #0b3a22;
    --beige: #f3ecdb;
    --ink: #2b2b2b;
    --white: #ffffff;
    --backdrop: #767676;
  }
  * { margin: 0; padding: 0; box-sizing: border-box; }
  html, body { width: 931px; height: 1200px; overflow: hidden; background: var(--backdrop); }
  .flyer {
    position: absolute; left: 85px; top: 73px; width: 760px; height: 1055px;
    background: var(--white); overflow: hidden;
    font-family: "Poppins", sans-serif; color: var(--ink);
  }
  .shapes { position: absolute; inset: 0; }
  .abs { position: absolute; }

  .headline {
    left: 63px; top: 40px;
    font-family: "Montserrat", sans-serif; font-weight: 800; color: var(--white);
    font-size: 42.5px; line-height: 41.6px; letter-spacing: -0.2px;
  }
  .subhead {
    left: 62px; top: 178px;
    font-family: "Montserrat", sans-serif; font-weight: 600; color: var(--white);
    font-size: 29px; line-height: 26px;
  }

  .hero-photo {
    left: 468px; top: 46px; width: 294px; height: 294px; border-radius: 50%;
    background: linear-gradient(160deg, #efeae2 0%, #e6dccb 35%, #d6a635 62%, #8a6a3c 85%, #3a2f28 100%);
    border: 6px solid var(--white);
  }
  .mind-art {
    left: 14px; top: 312px; width: 322px; height: 322px; border-radius: 50%;
    background: linear-gradient(135deg, #1aa894 0%, #0f9482 40%, #6cc463 75%, #a6dc6a 100%);
  }

  .conditions { list-style: none; }
  .conditions li {
    position: absolute; height: 36px; display: flex; align-items: center;
    font-weight: 600; font-size: 19px; color: var(--ink);
  }
  .conditions .dot {
    width: 34px; height: 34px; border-radius: 50%; background: var(--forest);
    border: 2px solid var(--lime); margin-right: 22px; flex: none;
    display: flex; align-items: center; justify-content: center;
  }
  .conditions .dot::after {
    content: ""; width: 12px; height: 12px; border: 2px solid var(--white); border-radius: 50%;
  }

  .experts-banner {
    left: 179px; top: 650px; width: 406px; height: 31px; border-radius: 16px;
    background: var(--forest); color: var(--white);
    font-weight: 600; font-size: 18.5px; text-align: center; line-height: 31px;
  }

  .provider-card {
    position: absolute; top: 749px; width: 141px; height: 122px; background: var(--beige);
  }
  .provider-photo {
    position: absolute; top: 698px; width: 110px; height: 123px; border-radius: 10px;
  }
  .provider-name {
    position: absolute; top: 826px; width: 141px; text-align: center;
    color: var(--forest); font-weight: 600; font-size: 15.5px; line-height: 18px;
  }
  .provider-name small {
    display: block; font-weight: 500; font-size: 12px; line-height: 15px; color: var(--forest);
  }

  .pill {
    top: 895px; height: 46px; border: 2px solid var(--lime); border-radius: 12px;
    color: var(--white); font-family: "Montserrat", sans-serif; font-weight: 700;
    font-size: 14.5px; line-height: 15px; padding: 7px 0 0 20px;
  }
  .pill .tick {
    position: absolute; left: -10px; top: 12px; width: 20px; height: 20px; border-radius: 50%;
    background: var(--forest); border: 2px solid var(--lime);
  }
  .pill .tick svg { position: absolute; left: 3px; top: 4px; }

  .hours { left: 286px; top: 955px; color: var(--white); font-weight: 600; }
  .hours .label { font-size: 14px; line-height: 20px; }
  .hours .row { font-size: 15.5px; line-height: 20px; display: flex; align-items: center; gap: 5px; }
  .hours .row i { width: 8px; height: 8px; background: var(--lime); display: inline-block; }
  .hours .row i.round { border-radius: 50%; }

  .contact { left: 423px; top: 955px; color: var(--white); }
  .contact .row { display: flex; align-items: center; gap: 6px; font-size: 12px; line-height: 20px; }
  .contact .row.phone { font-weight: 700; font-size: 16.5px; }
  .contact .ico {
    width: 12px; height: 12px; border-radius: 50%; background: var(--lime);
    display: inline-flex; align-items: center; justify-content: center; flex: none;
  }

  .brand { left: 52px; top: 928px; width: 180px; text-align: center; }
  .brand .mark { width: 40px; height: 40px; border-radius: 50%; background: var(--teal); margin: 0 auto 10px; }
  .brand .name {
    font-family: "Poppins", sans-serif; font-weight: 600; color: var(--teal);
    font-size: 19px; line-height: 22px; letter-spacing: 0.5px;
  }
</style>
</head>
<body>
<main class="flyer">
  <svg class="shapes" width="760" height="1055" viewBox="0 0 760 1055" aria-hidden="true">
    <path d="M0 0 H749 L760 -6 V70 L700 130 L470 290 C380 300 300 298 256 293 C150 285 60 260 0 225 Z" fill="var(--teal)"/>
    <circle cx="616" cy="193" r="152" fill="none" stroke="var(--lime)" stroke-width="4" stroke-dasharray="330 625" transform="rotate(5 616 193)"/>
    <g stroke="#bdbdbd" stroke-width="1" stroke-dasharray="3 2">
      <line x1="345" y1="374" x2="733" y2="374"/>
      <line x1="345" y1="424" x2="733" y2="424"/>
      <line x1="355" y1="475" x2="733" y2="475"/>
      <line x1="345" y1="524" x2="733" y2="524"/>
      <line x1="345" y1="574" x2="733" y2="574"/>
    </g>
    <path d="M205 810 H556 V869 H205 Z" fill="var(--forest)"/>
    <path d="M104 869 H670 L760 945 V1055 H0 V869 Z" fill="var(--forest)"/>
    <path d="M0 882 C110 875 250 930 253 1055 H0 Z" fill="var(--white)"/>
  </svg>

  <h1 class="abs headline">COMPREHENSIVE<br>MENTAL HEALTH<br>EVALUATIONS</h1>
  <p class="abs subhead">Medication management<br>&amp; psychotherapy</p>

  <div class="abs hero-photo" role="img" aria-label="Photo of a smiling woman in a yellow top looking at her phone"></div>
  <div class="abs mind-art" role="img" aria-label="Illustration of a head profile with a brain and green leaves"></div>

  <ul class="conditions">
    <li style="left:270px;top:335px"><span class="dot"></span>ADD/ADHD</li>
    <li style="left:300px;top:383px"><span class="dot"></span>Bipolar Disorder</li>
    <li style="left:317px;top:432px"><span class="dot"></span>Prompt Appointments</li>
    <li style="left:317px;top:481px"><span class="dot"></span>Depression, Anxiety</li>
    <li style="left:300px;top:531px"><span class="dot"></span>Schizophrenia</li>
    <li style="left:270px;top:574px"><span class="dot"></span>Grief Reaction and others</li>
  </ul>

  <h2 class="abs experts-banner">Medication Management Experts</h2>

  <section class="providers">
    <div class="provider-card" style="left:78px"></div>
    <div class="provider-card" style="left:232px"></div>
    <div class="provider-card" style="left:387px"></div>
    <div class="provider-card" style="left:540px"></div>
    <div class="provider-photo" style="left:95px;background:linear-gradient(180deg,#6d7478 0%,#8b8f92 45%,#c9d6e8 100%)" role="img" aria-label="Portrait of Evan Marsh"></div>
    <div class="provider-photo" style="left:249px;background:linear-gradient(180deg,#5e6468 0%,#7a6f68 45%,#1c1c1e 100%)" role="img" aria-label="Portrait of Lauren Pryce"></div>
    <div class="provider-photo" style="left:403px;background:linear-gradient(180deg,#5a6064 0%,#8a7a72 45%,#3b5478 100%)" role="img" aria-label="Portrait of Dale Whitford"></div>
    <div class="provider-photo" style="left:556px;background:linear-gradient(180deg,#6a7075 0%,#9a8f8a 45%,#1e1e20 100%)" role="img" aria-label="Portrait of Maren Ashby"></div>
    <p class="provider-name" style="left:78px">Evan Marsh<small>PMHNP - BC</small></p>
    <p class="provider-name" style="left:232px">Lauren Pryce<small>PMHNP - BC</small></p>
    <p class="provider-name" style="left:387px">Dale Whitford<small>PMHNP - BC</small></p>
    <p class="provider-name" style="left:540px">Maren Ashby<small>PMHNP-BC, DNP</small></p>
  </section>

  <div class="abs pill" style="left:275px;width:157px">
    <span class="tick"><svg width="10" height="8" viewBox="0 0 10 8"><path d="M1 4 L4 7 L9 1" fill="none" stroke="var(--lime)" stroke-width="1.8"/></svg></span>
    PROMPT<br>APPOINTMENTS
  </div>
  <div class="abs pill" style="left:452px;width:170px">
    <span class="tick"><svg width="10" height="8" viewBox="0 0 10 8"><path d="M1 4 L4 7 L9 1" fill="none" stroke="var(--lime)" stroke-width="1.8"/></svg></span>
    VIRTUAL AND<br>IN-PERSON VISITS
  </div>

  <div class="abs hours">
    <div class="label">HOURS:</div>
    <div class="row"><i></i>Mon - Thur</div>
    <div class="row"><i class="round"></i>7AM - 6PM</div>
  </div>

  <div class="abs contact">
    <div class="row phone"><span class="ico"><svg width="7" height="7" viewBox="0 0 10 10"><path d="M2 1 L4 3 L3 4 C4 6 5 7 6 7 L7 6 L9 8 L8 9 C4 9 1 6 1 2 Z" fill="var(--forest)"/></svg></span>(208)555-7193</div>
    <div class="row"><span class="ico"><svg width="6" height="8" viewBox="0 0 6 8"><path d="M3 8 C1 5 0 4 0 3 A3 3 0 0 1 6 3 C6 4 5 5 3 8 Z" fill="var(--forest)"/></svg></span>412 E Marlowe Coeur d'Alene</div>
    <div class="row"><span class="ico"><svg width="8" height="8" viewBox="0 0 8 8"><circle cx="4" cy="4" r="3" fill="none" stroke="var(--forest)" stroke-width="1"/><line x1="1" y1="4" x2="7" y2="4" stroke="var(--forest)" stroke-width="1"/></svg></span>website: BrightLoftCare.com</div>
  </div>

  <div class="abs brand">
    <div class="mark"></div>
    <div class="name">BRIGHT LOFT CARE</div>
  </div>
</main>
</body>
</html>
```